Nanotechnology meets nature cosmetic company needs label design. Name of the company is BriolaGrove

We are a cosmetic brand that combines nanotechnology with nature in the form of hemp extracts and essential oils, creating products that provide pain relief as well as stress reduction and relaxation. We have three different products and need three separate labels. We have a logo and would like to incorporate that into the label design. The colors are teal, black and gray. We would like to convey a message of combining nature with cutting edge cosmetic technology.
1. Topical pain lotion
2. Bath soak
3. Massage lotion
The logo is attached and I would just like the logo used and not the text below. The colors of the logo should be teal cross and "V" inside the gray lines that make up the circle with black color inside the circle. If this can't be done, I can send another logo.

```html
<!DOCTYPE html>
<html lang="en">
<head>
<meta charset="utf-8">
<title>BriolaGrove Product Labels</title>
<link href="https://fonts.googleapis.com/css2?family=Poppins:wght@300;400&display=swap" rel="stylesheet">
<style>
  :root {
    --canvas: #ffffff;
    --label-black: #0b0b0b;
    --label-edge: #2e2e2e;
    --teal: #17b3a3;
    --teal-light: #7fe3d6;
    --white: #f4f4f4;
  }
  * { margin: 0; padding: 0; box-sizing: border-box; }
  html, body {
    width: 1083px; height: 1200px; overflow: hidden;
    background: var(--canvas);
    font-family: "Poppins", sans-serif;
  }
  .label-row {
    position: absolute; top: 403px; left: 115px;
    display: flex; gap: 25px;
  }
  .label {
    position: relative;
    width: 268px; height: 652px;
    background: linear-gradient(90deg, var(--label-black) 0%, var(--label-black) 58%, var(--label-edge) 100%);
    color: var(--white);
    text-align: center;
  }
  .brand {
    position: absolute; top: 114px; left: 0; right: 0;
    display: flex; align-items: center; justify-content: center; gap: 8px;
    font-weight: 400; font-size: 24px; line-height: 32px; color: var(--teal);
  }
  .brand-dot {
    width: 12px; height: 12px; border-radius: 50%;
    background: var(--teal);
  }
  .title-top {
    position: absolute; top: 204px; left: 0; right: 0;
    font-weight: 400; font-size: 40px; line-height: 44px; color: var(--teal);
  }
  .title-main {
    position: absolute; top: 246px; left: 0; right: 0;
    font-weight: 300; font-size: 38px; line-height: 44px; color: var(--white);
    white-space: nowrap;
  }
  .tagline {
    position: absolute; top: 304px; left: 0; right: 0;
    padding-left: 2.6px;
    font-weight: 300; font-size: 12.5px; letter-spacing: 2.6px; line-height: 17px;
  }
  .wave-band {
    position: absolute; top: 356px; left: 0; right: 0; height: 138px;
    background: radial-gradient(ellipse at 55% 50%, rgba(127,227,214,0.55) 0%, rgba(23,179,163,0.35) 40%, rgba(11,11,11,0) 75%);
  }
  .nature-note {
    position: absolute; top: 512px; left: 0; right: 0;
    font-weight: 300; font-size: 13px; line-height: 16px;
  }
  .nature-note .accent { color: var(--teal); display: block; }
  .features {
    position: absolute; top: 561px; left: 8px; right: 8px;
    display: flex;
    border-top: 1px solid var(--teal); border-bottom: 1px solid var(--teal);
    font-weight: 300; font-size: 11.5px; line-height: 15px;
  }
  .features span { flex: 1; padding: 4px 0; white-space: nowrap; }
  .features span + span { border-left: 1px solid var(--teal); }
  .net-weight {
    position: absolute; top: 607px; left: 0; right: 0;
    font-weight: 300; font-size: 11.5px; line-height: 15px;
  }
</style>
</head>
<body>
  <div class="label-row">
    <section class="label label--pain-lotion">
      <div class="brand"><span class="brand-dot"></span>BriolaGrove</div>
      <div class="title-top">Topical</div>
      <div class="title-main">Pain Lotion</div>
      <div class="tagline">STRESS REDUCTION<br>&amp; RELAXATION</div>
      <div class="wave-band" role="img" aria-label="Teal dotted particle wave decoration"></div>
      <p class="nature-note">With nature in the form of<span class="accent">Hemp Extracts &amp; Essential Oils</span></p>
      <div class="features"><span>Fast Acting</span><span>Non-Greasy</span><span>No Burning</span></div>
      <div class="net-weight">Net wt. 4oz. (113.4g)</div>
    </section>
    <section class="label label--bath-soak">
      <div class="brand"><span class="brand-dot"></span>BriolaGrove</div>
      <div class="title-top">Hemp</div>
      <div class="title-main">Bath Soak</div>
      <div class="tagline">STRESS REDUCTION<br>&amp; RELAXATION</div>
      <div class="wave-band" role="img" aria-label="Teal dotted particle wave decoration"></div>
      <p class="nature-note">With nature in the form of<span class="accent">Hemp Extracts &amp; Essential Oils</span></p>
      <div class="features"><span>Fast Acting</span><span>Non-Greasy</span><span>No Burning</span></div>
      <div class="net-weight">Net wt. 4oz. (113.4g)</div>
    </section>
    <section class="label label--massage-lotion">
      <div class="brand"><span class="brand-dot"></span>BriolaGrove</div>
      <div class="title-top">Massage</div>
      <div class="title-main">Lotion</div>
      <div class="tagline">STRESS REDUCTION<br>&amp; RELAXATION</div>
      <div class="wave-band" role="img" aria-label="Teal dotted particle wave decoration"></div>
      <p class="nature-note">With nature in the form of<span class="accent">Hemp Extracts &amp; Essential Oils</span></p>
      <div class="features"><span>Fast Acting</span><span>Non-Greasy</span><span>No Burning</span></div>
      <div class="net-weight">Net wt. 4oz. (113.4g)</div>
    </section>
  </div>
</body>
</html>
```